Business Card Design Project

Actor, Producer, Vocal Coach, Choral Director, Song WriterPhone: (215) 555-0142 Fax: (215) 856-3933Email: waltierblocker@gmail.comFacebook: facebook.com/waltier.blockerTwitter: @thedf482

Industry/Entity Type

Business

Contact Information for Business Card

Business Cards that include my picture

Colors

Designer to choose colors to be used in the design.

```html
<!DOCTYPE html>
<html lang="en">
<head>
<meta charset="utf-8">
<title>Dorian Fellsmore – Business Card</title>
<link rel="stylesheet" href="https://fonts.googleapis.com/css2?family=Cinzel:wght@600&family=Source+Sans+3:wght@400&display=swap">
<style>
  :root {
    --page-bg: #2f2f2f;
    --card-top: #c9c6be;
    --card-band: #f3f6fd;
    --ink: #111111;
    --portrait-top: #d3d0c9;
    --portrait-bottom: #eeeef0;
  }
  * { margin: 0; padding: 0; box-sizing: border-box; }
  html, body {
    width: 1200px;
    height: 900px;
    overflow: hidden;
    background: var(--page-bg);
  }
  .business-card {
    position: absolute;
    left: 381px;
    top: 315px;
    width: 439px;
    height: 271px;
    border-radius: 10px;
    overflow: hidden;
    background: var(--card-top);
    font-family: "Source Sans 3", sans-serif;
    color: var(--ink);
  }
  .portrait {
    position: absolute;
    left: 0;
    top: 50px;
    width: 197px;
    height: 181px;
    background: linear-gradient(180deg, var(--portrait-top) 0%, var(--portrait-bottom) 100%);
  }
  .identity {
    position: absolute;
    left: 215px;
    top: 92px;
  }
  .identity__name {
    font-family: "Cinzel", serif;
    font-weight: 600;
    font-size: 17px;
    letter-spacing: 0.2px;
    line-height: 21px;
    white-space: nowrap;
  }
  .identity__roles {
    font-size: 12.5px;
    line-height: 16px;
    margin-top: 2px;
  }
  .contact-list {
    position: absolute;
    left: 215px;
    top: 167px;
    list-style: none;
    font-size: 12.5px;
    line-height: 16.5px;
  }
  .contact-list__item {
    display: flex;
    align-items: center;
    gap: 4px;
    white-space: nowrap;
  }
  .contact-list__icon {
    width: 11px;
    height: 11px;
    fill: var(--ink);
    flex: none;
  }
  .social-band {
    position: absolute;
    left: 0;
    bottom: 0;
    width: 100%;
    height: 41px;
    background: var(--card-band);
  }
  .social-link {
    position: absolute;
    top: 11px;
    display: flex;
    align-items: center;
    gap: 5px;
    font-size: 13px;
    white-space: nowrap;
  }
  .social-link--short { left: 44px; }
  .social-link--page { left: 214px; }
  .social-link__mark {
    width: 18px;
    height: 16px;
    background: var(--ink);
    flex: none;
  }
</style>
</head>
<body>
  <section class="business-card">
    <div class="portrait" role="img" aria-label="Portrait photo of the card owner in a white shirt and pink tie"></div>

    <div class="identity">
      <h1 class="identity__name">DORIAN FELLSMORE</h1>
      <p class="identity__roles">Actor, Producer, Vocal Coach,<br>Choral Director, Song Writer</p>
    </div>

    <ul class="contact-list">
      <li class="contact-list__item">
        <svg class="contact-list__icon" viewBox="0 0 12 12" aria-hidden="true"><path d="M2.4 0.6 L4.2 2.6 L3.2 4 C3.9 5.6 5.4 7.2 7.9 8.7 L9.2 7.7 L11.4 9.5 L10.1 11.3 C5.6 11 1 6.4 0.6 1.9 Z"/></svg>
        <span>(215) 555-0142</span>
      </li>
      <li class="contact-list__item">
        <svg class="contact-list__icon" viewBox="0 0 12 12" aria-hidden="true"><path d="M3 1 H8 L9 2 V4 H3 Z M1 4.5 H11 V10.5 H1 Z M3 7 H9 V8 H3 Z" fill-rule="evenodd"/></svg>
        <span>(215) 555-0187</span>
      </li>
      <li class="contact-list__item">
        <svg class="contact-list__icon" viewBox="0 0 12 12" aria-hidden="true"><path d="M0.5 2.5 H11.5 V9.5 H0.5 Z M1.2 3 L6 6.6 L10.8 3 Z" fill-rule="evenodd"/></svg>
        <span>dorianfellsmore@postlane.net</span>
      </li>
    </ul>

    <footer class="social-band">
      <div class="social-link social-link--short">
        <span class="social-link__mark" aria-hidden="true"></span>
        <span>@thedf482</span>
      </div>
      <div class="social-link social-link--page">
        <span class="social-link__mark" aria-hidden="true"></span>
        <span>socialpage.net/dorian.fellsmore</span>
      </div>
    </footer>
  </section>
</body>
</html>
```